TA BRAMLEY BUSINESS CARD DESIGN PROJECT

We need to utilize our logo that was expertly created on PixelHarbor and now need to match this with a business card design.

```html
<!DOCTYPE html>
<html lang="en">
<head>
<meta charset="UTF-8">
<title>TA BRAMLEY Business Card</title>
<link rel="stylesheet" href="https://fonts.googleapis.com/css2?family=Montserrat:wght@400;600;700&display=swap">
<style>
  :root {
    --brand-blue: #0f57b0;
    --card-black: #151515;
    --ink-white: #ffffff;
    --page-bg: #d9d9d9;
  }
  * { margin: 0; padding: 0; box-sizing: border-box; }
  html, body { width: 1200px; height: 900px; overflow: hidden; }
  body {
    background: var(--page-bg);
    font-family: "Montserrat", sans-serif;
    position: relative;
  }
  .card {
    position: absolute;
    width: 560px;
    height: 320px;
    border-radius: 22px;
    overflow: hidden;
    box-shadow: 0 10px 28px rgba(0,0,0,0.25);
  }
  .card-front {
    left: 90px; top: 100px;
    background: var(--brand-blue);
    display: flex; align-items: center; justify-content: center;
  }
  .wordmark {
    color: var(--ink-white);
    font-weight: 700;
    letter-spacing: 0.14em;
    display: flex; align-items: center;
    white-space: nowrap;
  }
  .card-front .wordmark { font-size: 50px; gap: 20px; }
  .wordmark-dot {
    display: inline-block;
    border-radius: 50%;
    background: var(--ink-white);
    flex: none;
  }
  .card-front .wordmark-dot { width: 34px; height: 34px; }

  .card-back { left: 550px; top: 470px; background: var(--card-black); }
  .card-back .wave { position: absolute; inset: 0; width: 100%; height: 100%; }
  .card-back .wordmark {
    position: absolute; right: 34px; top: 26px;
    font-size: 24px; gap: 10px;
  }
  .card-back .wordmark-dot { width: 16px; height: 16px; }
  .divider {
    position: absolute; left: 238px; right: 34px; top: 210px;
    height: 1px; background: var(--brand-blue);
  }
  .person { position: absolute; left: 48px; top: 196px; }
  .person-name {
    color: var(--brand-blue); font-weight: 700;
    font-size: 20px; letter-spacing: 0.02em; line-height: 1.2;
  }
  .person-title { color: var(--ink-white); font-size: 14px; margin-top: 2px; line-height: 1.3; }
  .contact-list { list-style: none; margin-top: 10px; }
  .contact-list li {
    color: var(--ink-white); font-size: 12.5px; line-height: 1.3;
    display: flex; align-items: center; gap: 8px; margin-bottom: 2px;
  }
  .contact-list svg { width: 12px; height: 12px; fill: var(--brand-blue); flex: none; }
  .address {
    position: absolute; right: 34px; top: 226px;
    color: var(--ink-white); font-size: 13px; line-height: 1.45; text-align: right;
  }
</style>
</head>
<body>
  <section class="card card-front">
    <div class="wordmark"><span class="wordmark-dot"></span>TA BRAMLEY</div>
  </section>

  <section class="card card-back">
    <svg class="wave" viewBox="0 0 560 320" preserveAspectRatio="none" aria-hidden="true">
      <path d="M0 0 H560 V62 C470 108 330 116 190 132 C100 143 40 157 18 176 L0 176 Z" fill="#0f57b0"/>
      <path d="M560 78 C470 124 330 132 190 148 C110 158 52 172 32 190 L22 190 C42 168 104 152 188 140 C330 124 470 116 560 70 Z" fill="#0f57b0"/>
    </svg>
    <div class="wordmark"><span class="wordmark-dot"></span>TA BRAMLEY</div>
    <div class="divider"></div>
    <div class="person">
      <div class="person-name">OWEN HARLOW</div>
      <div class="person-title">Managing Director</div>
      <ul class="contact-list">
        <li><svg viewBox="0 0 24 24"><path d="M6.6 10.8a15 15 0 0 0 6.6 6.6l2.2-2.2c.3-.3.7-.4 1-.2 1.1.4 2.3.6 3.6.6.6 0 1 .4 1 1V20c0 .6-.4 1-1 1A17 17 0 0 1 3 4c0-.6.4-1 1-1h3.5c.6 0 1 .4 1 1 0 1.3.2 2.5.6 3.6.1.3 0 .7-.2 1z"/></svg>555 210 447</li>
        <li><svg viewBox="0 0 24 24"><path d="M2 5h20v14H2z M2 5l10 8 10-8"/></svg>hello@tabramley.com</li>
        <li><svg viewBox="0 0 24 24"><circle cx="12" cy="12" r="10"/></svg>www.tabramley.com</li>
      </ul>
    </div>
    <div class="address">418 Larkspur Lane SE<br>Marietta, GA 30060</div>
  </section>
</body>
</html>
```